Business Card Design

I already have a company logo for my company. I have a logo for the manufacturer we represent. I want a professional business card design.

```html
<!DOCTYPE html>
<html lang="en">
<head>
<meta charset="utf-8">
<title>Business Card – Halden Alert Systems LLC</title>
<link rel="stylesheet" href="https://fonts.googleapis.com/css2?family=Lato:wght@400;700&family=Michroma&display=swap">
<style>
  :root {
    --page-bg: #d9d9db;
    --card-bg: #1f1f21;
    --red: #e8262c;
    --gold: #d9a514;
    --silver-light: #f2f2f2;
    --silver-mid: #a9a9ab;
    --silver-dark: #6e6e70;
    --text-light: #f4f4f4;
  }
  * { box-sizing: border-box; margin: 0; padding: 0; }
  html, body { width: 1200px; height: 982px; overflow: hidden; }
  body {
    background: var(--page-bg);
    font-family: "Lato", sans-serif;
    display: flex;
    flex-direction: column;
    align-items: center;
    justify-content: center;
    gap: 40px;
  }
  .card {
    position: relative;
    width: 760px;
    height: 434px;
    background: var(--card-bg);
    border-radius: 22px;
    overflow: hidden;
    box-shadow: 0 10px 28px rgba(0,0,0,.35);
  }
  /* Front side */
  .card--front { display: flex; align-items: center; justify-content: center; }
  .brand-mark { display: flex; align-items: center; gap: 14px; }
  .brand-mark__square { width: 22px; height: 22px; background: var(--red); }
  .brand-mark__name {
    font-family: "Lato", sans-serif;
    font-weight: 700;
    font-size: 38px;
    letter-spacing: 2px;
    color: var(--red);
    text-transform: uppercase;
  }
  /* Back side */
  .holder { position: absolute; left: 56px; top: 54px; }
  .holder__name {
    font-family: "Michroma", sans-serif;
    font-size: 34px;
    letter-spacing: 2px;
    color: var(--silver-mid);
    background: linear-gradient(180deg, var(--silver-light), var(--silver-mid) 60%, var(--silver-dark));
    -webkit-background-clip: text;
    background-clip: text;
    -webkit-text-fill-color: transparent;
  }
  .holder__title { font-size: 22px; color: var(--red); margin-top: 2px; }
  .divider {
    position: absolute; left: 56px; right: 56px; top: 150px; height: 2px;
    background: linear-gradient(90deg, var(--silver-dark), var(--silver-light) 55%, var(--silver-dark) 80%, #fff);
  }
  .contact-list { position: absolute; left: 56px; top: 178px; list-style: none; }
  .contact-list li {
    display: flex; align-items: center; gap: 14px;
    font-size: 21px; color: var(--text-light); line-height: 36px;
  }
  .contact-list svg { width: 18px; height: 18px; fill: var(--red); flex: none; }
  .company {
    position: absolute; right: 56px; top: 178px; text-align: right;
  }
  .company .brand-mark { justify-content: flex-end; margin-bottom: 30px; }
  .company .brand-mark__name { font-size: 24px; letter-spacing: 1px; }
  .company .brand-mark__square { width: 16px; height: 16px; }
  .company__name { font-size: 21px; color: var(--red); line-height: 30px; }
  .company__line { font-size: 20px; color: var(--text-light); line-height: 30px; }
  .edge-band { position: absolute; left: 0; right: 0; bottom: 0; height: 20px; display: flex; }
  .edge-band__silver { flex: 0 0 62%; background: linear-gradient(90deg, var(--silver-dark), var(--silver-light) 30%, var(--silver-mid) 70%, var(--silver-dark)); }
  .edge-band__slashes { flex: 0 0 60px; background: var(--card-bg); }
  .edge-band__gold { flex: 1; background: linear-gradient(90deg, #b88a0c, var(--gold)); }
</style>
</head>
<body>
  <section class="card card--front" aria-label="Card front">
    <div class="brand-mark">
      <span class="brand-mark__square"></span>
      <span class="brand-mark__name">Halden Alert Systems LLC</span>
    </div>
  </section>

  <section class="card card--back" aria-label="Card back">
    <div class="holder">
      <h1 class="holder__name">JOHN SMITH</h1>
      <p class="holder__title">Founder &amp; CEO</p>
    </div>
    <div class="divider"></div>

    <ul class="contact-list">
      <li><svg viewBox="0 0 24 24"><path d="M6.6 10.8a15.1 15.1 0 0 0 6.6 6.6l2.2-2.2a1 1 0 0 1 1-.25 11.4 11.4 0 0 0 3.6.57 1 1 0 0 1 1 1V20a1 1 0 0 1-1 1A17 17 0 0 1 3 4a1 1 0 0 1 1-1h3.5a1 1 0 0 1 1 1c0 1.25.2 2.45.57 3.57a1 1 0 0 1-.25 1z"/></svg>(123) 456-7890</li>
      <li><svg viewBox="0 0 24 24"><path d="M7 1h10a2 2 0 0 1 2 2v18a2 2 0 0 1-2 2H7a2 2 0 0 1-2-2V3a2 2 0 0 1 2-2zm0 3v14h10V4zm5 15.5a1 1 0 1 0 0 2 1 1 0 0 0 0-2z"/></svg>(123) 456-7890</li>
      <li><svg viewBox="0 0 24 24"><path d="M6 2h12v5H6zM4 8h16a2 2 0 0 1 2 2v7h-4v5H6v-5H2v-7a2 2 0 0 1 2-2zm4 8v4h8v-4z"/></svg>(123) 456-7890</li>
      <li><svg viewBox="0 0 24 24"><path d="M2 5h20v14H2zm2 2v.5l8 5 8-5V7l-8 5z"/></svg>info@yourwebsitehere.com</li>
    </ul>

    <div class="company">
      <div class="brand-mark">
        <span class="brand-mark__square"></span>
        <span class="brand-mark__name">Halden Alert Systems LLC</span>
      </div>
      <p class="company__name">Halden Alert Systems LLC</p>
      <p class="company__line">423 Street Address Here, City</p>
      <p class="company__line">State &amp; ZIP Code Country</p>
      <p class="company__line">www.yourwebsitehere.com</p>
    </div>

    <div class="edge-band">
      <div class="edge-band__silver"></div>
      <svg class="edge-band__slashes" viewBox="0 0 60 20" preserveAspectRatio="none">
        <polygon points="6,20 14,0 22,0 14,20" fill="#e8262c"/>
        <polygon points="22,20 30,0 38,0 30,20" fill="#e8262c"/>
        <polygon points="38,20 46,0 54,0 46,20" fill="#e8262c"/>
      </svg>
      <div class="edge-band__gold"></div>
    </div>
  </section>
</body>
</html>
```